Business Card Design Project

Looking to update our business cards. We have a logo with our slogan. We are an IT firm so we wouldlike a modern look.

Industry/Entity Type

Business

```html
<!DOCTYPE html>
<html lang="en">
<head>
<meta charset="utf-8">
<title>Norvale Tech — Business Card Options</title>
<link href="https://fonts.googleapis.com/css2?family=Questrial&family=Tinos&display=swap" rel="stylesheet">
<style>
  :root {
    --backdrop: #5b2f1f;
    --card-light: #e4e4e4;
    --card-light-edge: #d2d2d2;
    --band-light: #ececec;
    --card-dark: #2a2a2a;
    --card-dark-edge: #111111;
    --band-white: #ffffff;
    --brand-green: #5b7a2c;
    --ink: #1e1e1e;
    --label-dark: #111111;
    --label-light: #ffffff;
  }
  * { margin: 0; padding: 0; box-sizing: border-box; }
  html, body {
    width: 1200px;
    height: 1181px;
    overflow: hidden;
    background: var(--backdrop);
  }
  .canvas {
    position: relative;
    width: 1200px;
    height: 1181px;
  }
  .card {
    position: absolute;
    left: 199px;
    width: 802px;
    height: 462px;
    overflow: hidden;
    box-shadow: 0 6px 14px rgba(0, 0, 0, 0.45);
  }
  .card--light {
    top: 73px;
    background: radial-gradient(ellipse at 50% 45%, #f2f2f2 0%, var(--card-light) 55%, var(--card-light-edge) 100%);
  }
  .card--dark {
    top: 632px;
    height: 460px;
    background: radial-gradient(ellipse at 50% 30%, #3a3a3a 0%, var(--card-dark) 50%, var(--card-dark-edge) 100%);
  }
  .band {
    position: absolute;
    left: 0;
    width: 100%;
  }
  .card--light .band {
    top: 173px;
    height: 116px;
    background: linear-gradient(to bottom, #f4f4f4, var(--band-light) 50%, #e2e2e2);
    box-shadow: 0 1px 3px rgba(0, 0, 0, 0.18), 0 -1px 2px rgba(0, 0, 0, 0.08);
  }
  .card--dark .band {
    top: 173px;
    height: 114px;
    background: var(--band-white);
  }
  .brand__name {
    position: absolute;
    top: 192px;
    left: 0;
    width: 100%;
    font-family: "Questrial", sans-serif;
    font-size: 44px;
    line-height: 50px;
    letter-spacing: 0.08em;
    color: var(--brand-green);
    text-align: center;
  }
  .brand__slogan {
    position: absolute;
    top: 253px;
    left: 0;
    width: 100%;
    font-family: "Questrial", sans-serif;
    font-size: 17px;
    line-height: 20px;
    letter-spacing: 0.36em;
    color: var(--ink);
    text-align: center;
  }
  .option-label {
    position: absolute;
    left: -24px;
    width: 100%;
    text-align: center;
    font-family: "Tinos", serif;
    font-size: 36px;
    line-height: 40px;
  }
  .card--light .option-label { top: 374px; color: var(--label-dark); }
  .card--dark .option-label { top: 389px; left: -36px; color: var(--label-light); }
</style>
</head>
<body>
  <main class="canvas">
    <section class="card card--light" aria-label="Card option 1, light">
      <div class="band"></div>
      <p class="brand__name">NORVALE TECH</p>
      <p class="brand__slogan">SMART SUPPORT, EVERY DAY</p>
      <p class="option-label">1</p>
    </section>

    <section class="card card--dark" aria-label="Card option 2, dark">
      <div class="band"></div>
      <p class="brand__name">NORVALE TECH</p>
      <p class="brand__slogan">SMART SUPPORT, EVERY DAY</p>
      <p class="option-label">2</p>
    </section>
  </main>
</body>
</html>
```